New Zealand Marlborough Sauvignon Blanc wine packaging design

We need packaging design for our new wine brand, Dunmore Vale. The wine is a New Zealand Marlborough Sauvignon Blanc. We would like the packaging will portray elegance and style with an understated label. We are looking for a label that portrays the elegance of the French Riviera. The label should be round or pill shaped.
Updates

Industry/Entity Type

Wine

Font styles to use
Serif
Sans Serif

Requirements
Must have
• The words in order of importance: Dunmore Vale, Sauvignon Blanc, Marlborough, New Zealand. It should be fit to the bottle posted in the links
Nice to have
• a pill shape or circular shape
Should not have
• Illustrations of wine bottles, wine glasses, or grapes

```html
<!DOCTYPE html>
<html lang="en">
<head>
<meta charset="utf-8">
<title>Dunmore Vale Sauvignon Blanc Label</title>
<link href="https://fonts.googleapis.com/css2?family=Bodoni+Moda:wght@500;600;700&family=Pinyon+Script&display=swap" rel="stylesheet">
<style>
  :root {
    --canvas-bg: #ffffff;
    --label-base: #d9e3a3;
    --label-glow: #fbfdf4;
    --arch-line: #ffffff;
    --title-green: #7c9d2c;
    --title-edge: #5c7a1c;
    --script-green: #4f6a1e;
    --origin-green: #4d6619;
    --land-light: #b7cd66;
    --land-mid: #8f9a62;
    --land-grey: #a9a78c;
    --water-light: #ecece2;
    --water-fade: #eef4dc;
  }
  html, body {
    margin: 0;
    padding: 0;
    width: 1200px;
    height: 675px;
    overflow: hidden;
    background: var(--canvas-bg);
  }
  .canvas {
    position: relative;
    width: 1200px;
    height: 675px;
  }
  .label {
    position: absolute;
    left: 420px;
    top: 74px;
    width: 359px;
    height: 527px;
  }
  .label-shape {
    position: absolute;
    inset: 0;
    width: 359px;
    height: 527px;
  }
  .brand-name {
    position: absolute;
    left: 0;
    width: 100%;
    top: 160px;
    margin: 0;
    text-align: center;
    font-family: "Bodoni Moda", serif;
    font-weight: 700;
    font-size: 42px;
    line-height: 1;
    letter-spacing: -0.5px;
    color: var(--title-green);
  }
  .varietal {
    position: absolute;
    left: 0;
    width: 100%;
    top: 228px;
    margin: 0;
    text-align: center;
    font-family: "Pinyon Script", cursive;
    font-weight: 400;
    font-size: 29px;
    line-height: 1;
    color: var(--script-green);
  }
  .origin {
    position: absolute;
    left: 0;
    width: 100%;
    top: 437px;
    margin: 0;
    text-align: center;
    font-family: "Bodoni Moda", serif;
    font-weight: 600;
    font-size: 15px;
    line-height: 19px;
    color: var(--origin-green);
  }
</style>
</head>
<body>
  <main class="canvas">
    <section class="label">
      <svg class="label-shape" viewBox="0 0 359 527" xmlns="http://www.w3.org/2000/svg">
        <defs>
          <radialGradient id="label-glow" cx="180" cy="300" r="220" gradientUnits="userSpaceOnUse">
            <stop offset="0" stop-color="var(--label-glow)"/>
            <stop offset="0.45" stop-color="#eef3d2"/>
            <stop offset="1" stop-color="var(--label-base)"/>
          </radialGradient>
          <linearGradient id="landscape-tones" x1="0" y1="0" x2="0" y2="1">
            <stop offset="0" stop-color="var(--land-light)" stop-opacity="0.35"/>
            <stop offset="0.22" stop-color="var(--land-light)"/>
            <stop offset="0.42" stop-color="var(--land-mid)"/>
            <stop offset="0.5" stop-color="var(--land-grey)"/>
            <stop offset="0.62" stop-color="var(--water-light)"/>
            <stop offset="0.78" stop-color="#c9d6a4"/>
            <stop offset="1" stop-color="var(--water-fade)" stop-opacity="0"/>
          </linearGradient>
          <clipPath id="label-clip">
            <path d="M0,172 A179.5,172 0 0 1 359,172 L359,380 A179.5,147 0 0 1 0,380 Z"/>
          </clipPath>
        </defs>
        <path class="label-body" d="M0,172 A179.5,172 0 0 1 359,172 L359,380 A179.5,147 0 0 1 0,380 Z" fill="url(#label-glow)"/>
        <path class="label-arch" d="M31,312 L31,210 A148.5,179 0 0 1 328,210 L328,312" fill="none" stroke="var(--arch-line)" stroke-width="0.8"/>
        <g clip-path="url(#label-clip)">
          <rect class="landscape" x="0" y="298" width="359" height="160" fill="url(#landscape-tones)" role="img" aria-label="Soft layered green hills above a still lake with their reflection"/>
        </g>
      </svg>
      <h1 class="brand-name">Dunmore Vale</h1>
      <p class="varietal">Sauvignon Blanc</p>
      <p class="origin">Marlborough,<br>New Zealand</p>
    </section>
  </main>
</body>
</html>
```